Need to drive pregnant women to my 3d4d ultrasound studio where i provide 4d ultrasound with hyperalistic imaging and gender reveals

Industry/Entity Type

Healthcare

Font styles to use
Decorative
Script

Requirements
Must have
• My Company name Cielo de Nuestra Espera 4D. EVERYTHING HAS TO BE IN SPANISH
Nice to have
• SIMPLE AND NOT TOO BUSY
Should not have
• website

```html
<!DOCTYPE html>
<html lang="es">
<head>
<meta charset="UTF-8">
<title>Cielo de Nuestra Espera 4D — Valla</title>
<link href="https://fonts.googleapis.com/css2?family=Archivo+Black&family=Sora:wght@400;600;700&display=swap" rel="stylesheet">
<style>
  :root {
    --bg: #e9edf2;
    --paper: #ffffff;
    --purple: #a020f0;
    --pink: #ec3b86;
    --teal: #2f8f84;
    --ink: #111111;
    --scan-dark: #2a1204;
    --scan-mid: #a2530f;
    --scan-light: #e3962f;
    --skin-light: #f3d2c3;
    --skin-mid: #d9a48f;
  }
  * { margin: 0; padding: 0; box-sizing: border-box; }
  html, body { width: 1200px; height: 900px; overflow: hidden; background: var(--bg); }
  .canvas { position: relative; width: 1200px; height: 900px; }
  .billboard {
    position: absolute; left: 30px; top: 250px;
    width: 1140px; height: 400px;
    background: var(--paper); overflow: hidden;
    box-shadow: 0 8px 24px rgba(0,0,0,.12);
  }
  .billboard__imagery { position: absolute; inset: 0; width: 1140px; height: 400px; }
  .headline {
    position: absolute; left: 36px; top: 26px;
    font-family: "Archivo Black", sans-serif;
    font-size: 74px; line-height: 0.86; letter-spacing: 1px;
    text-transform: uppercase;
  }
  .headline span { display: block; }
  .headline__l1 { color: var(--purple); }
  .headline__l2 { color: var(--pink); }
  .headline__l3 { color: var(--teal); }
  .services-band {
    position: absolute; left: 0; top: 238px;
    width: 640px; height: 70px;
    background: var(--teal); color: #fff;
    font-family: "Sora", sans-serif; font-weight: 600;
    font-size: 17px; line-height: 1.3;
    padding: 10px 0 0 36px;
  }
  .contact {
    position: absolute; left: 36px; top: 330px;
    display: flex; align-items: center; gap: 16px;
    font-family: "Sora", sans-serif; color: var(--ink);
  }
  .contact__label { font-size: 22px; font-weight: 400; }
  .contact__icon { width: 22px; height: 28px; }
  .contact__phone { font-size: 38px; font-weight: 700; letter-spacing: .5px; }
</style>
</head>
<body>
<div class="canvas">
  <section class="billboard">
    <svg class="billboard__imagery" viewBox="0 0 1140 400">
      <defs>
        <radialGradient id="scanGlow" cx="0.55" cy="0.45" r="0.6">
          <stop offset="0" stop-color="var(--scan-light)"/>
          <stop offset="0.55" stop-color="var(--scan-mid)"/>
          <stop offset="1" stop-color="var(--scan-dark)"/>
        </radialGradient>
        <radialGradient id="babySkin" cx="0.5" cy="0.5" r="0.7">
          <stop offset="0" stop-color="var(--skin-light)"/>
          <stop offset="1" stop-color="var(--skin-mid)"/>
        </radialGradient>
      </defs>
      <polygon points="640,0 880,0 800,400 560,400" fill="url(#scanGlow)" role="img" aria-label="Imagen de ultrasonido 4D de un bebé en el vientre"/>
      <polygon points="888,0 1140,0 1140,400 808,400" fill="url(#babySkin)" role="img" aria-label="Fotografía de un recién nacido dormido"/>
      <polygon points="880,0 890,0 810,400 800,400" fill="#ffffff"/>
      <polygon points="540,0 650,0 610,230" fill="var(--pink)"/>
    </svg>

    <h1 class="headline">
      <span class="headline__l1">Cielo</span>
      <span class="headline__l2">de Nuestra</span>
      <span class="headline__l3">Espera 4D</span>
    </h1>

    <p class="services-band">
      Hacemos Ultrasonido en 3D/4d/5D ,10k Y Imagenes<br>
      Hyper-realistic Serviendo la area Oeste de Puerto Rico.
    </p>

    <div class="contact">
      <span class="contact__label">Para orientacion</span>
      <svg class="contact__icon" viewBox="0 0 24 30" aria-hidden="true">
        <path d="M6 2 L10 2 L11 9 L8 11 C9 16 11 20 14 23 L17 21 L22 25 L20 29 C10 28 2 16 3 5 Z" fill="var(--purple)"/>
      </svg>
      <span class="contact__phone">787-555-0142</span>
    </div>
  </section>
</div>
</body>
</html>
```